MS word document templates for consultancy

I need the following templates for my business using my logo as branding.

- General report template
- Letter head template
- Tender proposal template

The templates should be sleek and with minimal colors, but with a small amount of green and grey where appropriate (as per attached logo and email signature). Font should be consistent with the text in the email signature.

```html
<!DOCTYPE html>
<html lang="en">
<head>
<meta charset="UTF-8">
<title>Tender Proposal Cover – Northlane Advisory</title>
<link rel="stylesheet" href="https://fonts.googleapis.com/css2?family=Montserrat:wght@300;400;500;700;800&display=swap">
<style>
  :root {
    --brand-green: #2a9145;
    --ink: #1d1d1d;
    --slate: #565656;
    --muted: #5f5f5f;
    --paper: #ffffff;
    --backdrop: #bdbdbd;
    --font-main: 'Montserrat', Arial, sans-serif;
  }
  * { box-sizing: border-box; margin: 0; padding: 0; }
  html, body {
    width: 780px;
    height: 1200px;
    overflow: hidden;
    background: var(--backdrop);
    font-family: var(--font-main);
  }
  .cover {
    position: absolute;
    left: 40px;
    top: 147px;
    width: 700px;
    height: 906px;
    background: var(--paper);
    overflow: hidden;
  }
  .band {
    position: absolute;
    left: 0;
    width: 100%;
    height: 29px;
    background: var(--brand-green);
    z-index: 1;
  }
  .band--top { top: 0; }
  .band--bottom { bottom: 0; }
  .tab {
    position: absolute;
    left: 130px;
    width: 442px;
    height: 30px;
    background: var(--paper);
    z-index: 2;
  }
  .tab--top { top: 17px; border-radius: 18px 18px 0 0; }
  .tab--bottom { bottom: 20px; border-radius: 0 0 18px 18px; }

  .masthead {
    position: absolute;
    top: 38px;
    left: 0;
    width: 100%;
    text-align: center;
    z-index: 3;
  }
  .masthead__name {
    font-size: 34px;
    font-weight: 400;
    color: var(--ink);
    letter-spacing: 0.2px;
    line-height: 44px;
  }
  .masthead__year {
    margin-top: 12px;
    font-size: 34px;
    font-weight: 400;
    color: var(--brand-green);
    line-height: 40px;
  }

  .title-block {
    position: absolute;
    top: 370px;
    left: 0;
    width: 100%;
    text-align: center;
  }
  .title-block__main {
    font-size: 72px;
    font-weight: 800;
    color: var(--brand-green);
    letter-spacing: 2px;
    line-height: 84px;
  }
  .title-block__sub {
    margin-top: -8px;
    font-size: 41px;
    font-weight: 400;
    color: var(--slate);
    letter-spacing: 1.5px;
    line-height: 52px;
  }
  .contact-phone {
    margin-top: 16px;
    display: flex;
    flex-direction: column;
    align-items: center;
    gap: 8px;
  }
  .contact-phone__number {
    font-size: 16px;
    font-weight: 700;
    color: var(--brand-green);
  }

  .footer-info {
    position: absolute;
    bottom: 22px;
    left: 0;
    width: 100%;
    text-align: center;
    font-size: 15px;
    font-weight: 400;
    color: var(--muted);
    line-height: 22px;
    z-index: 3;
  }
  .footer-info__row {
    display: flex;
    justify-content: center;
    align-items: center;
    gap: 34px;
  }
  .footer-info__item {
    display: inline-flex;
    align-items: center;
    gap: 7px;
  }
</style>
</head>
<body>
  <main class="cover">
    <div class="band band--top"></div>
    <div class="tab tab--top"></div>

    <header class="masthead">
      <p class="masthead__name">Northlane Advisory</p>
      <p class="masthead__year">2025</p>
    </header>

    <section class="title-block">
      <h1 class="title-block__main">TENDER</h1>
      <h2 class="title-block__sub">PROPOSAL</h2>
      <div class="contact-phone">
        <svg width="15" height="15" viewBox="0 0 16 16" aria-hidden="true">
          <circle cx="8" cy="8" r="8" fill="var(--brand-green)"/>
          <path d="M5.2 4.3c.3-.3.7-.3.9 0l.9 1.2c.2.3.2.6 0 .9l-.5.5c.4.9 1.1 1.6 2 2l.5-.5c.3-.2.6-.2.9 0l1.2.9c.3.2.3.6 0 .9l-.6.6c-.5.5-1.3.5-2 .2-1.7-.8-3-2.1-3.8-3.8-.3-.7-.3-1.5.2-2z" fill="#fff"/>
        </svg>
        <span class="contact-phone__number">0400 555 019</span>
      </div>
    </section>

    <div class="band band--bottom"></div>
    <div class="tab tab--bottom"></div>

    <footer class="footer-info">
      <div class="footer-info__row">
        <span class="footer-info__item">
          <svg width="9" height="7" viewBox="0 0 9 7" aria-hidden="true"><rect width="9" height="7" rx="1" fill="var(--muted)"/><path d="M0.5 1l4 3 4-3" stroke="#fff" stroke-width="0.8" fill="none"/></svg>
          info@northlaneadvisory.com
        </span>
        <span class="footer-info__item">
          <svg width="8" height="8" viewBox="0 0 8 8" aria-hidden="true"><circle cx="4" cy="4" r="4" fill="var(--muted)"/></svg>
          www.northlaneadvisory.com
        </span>
      </div>
      <div class="footer-info__row">
        <span class="footer-info__item">
          <svg width="8" height="10" viewBox="0 0 8 10" aria-hidden="true"><path d="M4 0a3 3 0 0 1 3 3c0 2.2-3 6-3 6S1 5.2 1 3a3 3 0 0 1 3-3z" fill="var(--muted)"/><circle cx="4" cy="3" r="1.1" fill="#fff"/></svg>
          Dummy City, Dummy Country
        </span>
      </div>
    </footer>
  </main>
</body>
</html>
```